Brenvik Systems PowerPoint Template

Project Title: Professional & Functional PowerPoint Template (.potx) – Brenvik Systems Rebrand

Project Overview:
Brenvik Systems has recently undergone a complete rebranding, including a new logo, website, and visual identity. We need a professional, high-end PowerPoint Template (.potx) that reflects our new look while being highly functional for everyday use.

We previously had a design created, but it was built incorrectly (static images, oversized file, no Master Slides). The goal of this project is to take our new aesthetic and build a "workable" template where layouts are controlled by Master Slides and text is easily editable.

Style & Brand Direction:
The template must be an extension of our new website: https://www.brenvik-systems.example/

Aesthetic: Modern, clean, high-tech, and "Industrial Tech."

Color Palette: Please pull the primary blues, greys, and accent colors directly from the website.

Imagery/Graphics: Use clean lines and subtle tech-inspired gradients. Avoid "clutter."

Tone: Innovative, precise, and professional.

Technical Requirements (Crucial)
Format: Must be delivered as a PowerPoint Template file (** .potx **).

Functionality: All layouts must be built using Slide Masters. Users should be able to click "New Slide" and choose from specific layouts.

Native Elements: Do NOT use full-page background images for text areas. Bullet points must use native PowerPoint list functionality (not individual text boxes).

File Size: The template must be optimized and lightweight.

Fonts: Use standard professional fonts or provide the specific web-safe equivalent used on our site (e.g., Montserrat, Open Sans, etc.).

Required Slide Layouts
Please include a minimum of 10–12 Master layouts, including:
*Title Slide (2-3 variations: Dark and Light)
*Agenda/Table of Contents
*Section Header/Divider Slides
*Standard Text/Bullet Slide
*Two-Column Text Slide
*Image + Text Layouts (Left/Right variations)
*Data/Chart Slide (Styled bar/pie charts that match the brand)
*Process/Timeline Slide (Infographic style)
*Section slide

Attachments Provided
Brand Assets (.zip): Contains our new logo in various formats.

Inspiration/Existing PPT: We have attached the previous design created by our web agency. Note: Use this for visual inspiration ONLY. Do not copy the file structure, as it is technically flawed.

Deliverables
Final .potx file.

All used icons or custom graphics in vector format (if applicable).

Instruction note on any specific fonts used.

Target Market(s)

Internal communication and external (investors, customers)

Industry/Entity Type

Semiconductor, Automotive

Requirements
Must have
• A potx file

```html
<!DOCTYPE html>
<html lang="en">
<head>
<meta charset="utf-8">
<title>Brenvik Systems – Presentation Template</title>
<link href="https://fonts.googleapis.com/css2?family=Inter:wght@400;500;600;700&family=Roboto+Mono:wght@400&display=swap" rel="stylesheet">
<style>
:root{
  --stage:#808080;
  --paper:#ffffff;
  --ink:#1b1b1d;
  --ink-soft:#2d2d30;
  --rule:#b9b9bd;
  --blue:#1f4cf0;
  --blue-bright:#2656ff;
  --slice-1:#1846e8;
  --slice-2:#4068ee;
  --slice-3:#7f97f3;
  --slice-4:#b2c1f8;
  --photo-mid:#4a5366;
}
*{margin:0;padding:0;box-sizing:border-box}
html,body{width:1027px;height:1200px;overflow:hidden;background:var(--stage)}
body{position:relative;font-family:"Inter",Arial,sans-serif;color:var(--ink)}
.slide{position:absolute;width:472px;height:265px;background:var(--paper);overflow:hidden}
.col-a{left:31px}.col-b{left:523px}
.row-1{top:36px}.row-2{top:320px}.row-3{top:601px}.row-4{top:887px}
.abs{position:absolute}
.mono{font-family:"Roboto Mono",monospace}
.slide-title{position:absolute;left:18px;top:14px;font-size:28px;font-weight:500;letter-spacing:-.3px}
.footer{position:absolute;left:20px;right:20px;top:243px;height:8px;display:flex;align-items:center;gap:4px;font-family:"Roboto Mono",monospace;font-size:5.3px;letter-spacing:.2px;color:var(--ink-soft)}
.footer .dot{width:3.5px;height:3.5px;background:var(--blue)}
.footer .line{flex:1;height:.5px;background:var(--rule);margin:0 10px}
.footer.on-blue{color:#fff}.footer.on-blue .dot{background:#fff}.footer.on-blue .line{background:rgba(255,255,255,.55)}
.wordmark{display:flex;align-items:center;gap:6px;font-weight:700;font-size:24px;letter-spacing:-.3px;color:var(--ink)}
.wordmark .mark{width:17px;height:17px;background:var(--blue)}
.photo{position:absolute}
.text-block{position:absolute;display:flex;flex-direction:column}
.lead{font-size:13px;line-height:17px;font-weight:400;color:var(--ink);letter-spacing:-.2px}
.body{font-size:8.4px;line-height:12px;color:var(--ink-soft)}
/* cover */
.cover-title{position:absolute;left:18px;top:157px;font-size:30px;line-height:32px;font-weight:500;letter-spacing:-.3px}
.cover-date{position:absolute;left:20px;top:236px;font-size:7.6px;display:flex;align-items:center;gap:4px}
.cover-date i,.contact i{display:inline-block;width:3.5px;height:3.5px;background:var(--blue)}
/* section */
.section{background:radial-gradient(circle at 50% 53%,#9ee0ff 0,#5fb4ff 14%,#3a7dff 30%,var(--blue-bright) 48%)}
.section-title{position:absolute;left:0;right:0;top:104px;text-align:center;color:#fff;font-size:44px;font-weight:500;letter-spacing:-.5px}
/* agenda */
.agenda-list{position:absolute;left:26px;top:74px;list-style:none;font-size:9.2px}
.agenda-list li{height:19.7px;display:flex}
.agenda-list span{width:19px}
/* pie labels */
.pie-label{position:absolute;text-align:center;font-size:6.6px;line-height:9px;transform:translateX(-50%);white-space:nowrap}
.pie-label b{font-weight:500;font-size:8px;display:block}
/* timeline */
.tl-year{position:absolute;top:135px;display:flex;align-items:center;gap:5px;font-size:11px}
.tl-year i{width:8px;height:8px;background:var(--blue)}
.tl-link{position:absolute;top:141px;height:.6px;background:var(--ink-soft)}
.tl-note{position:absolute;font-size:7.4px;line-height:10.5px;color:var(--ink-soft)}
/* about */
.feature{position:absolute;left:251px;display:flex;gap:11px}
.feature .icon{width:33px;height:33px;background:var(--blue);display:flex;align-items:center;justify-content:center;flex:none}
.feature h3{font-size:10px;font-weight:400;margin-top:-2px;margin-bottom:3px}
.feature p{font-size:7.4px;line-height:10.5px;color:var(--ink-soft);width:160px}
.contact{position:absolute;left:20px;font-size:7.4px;display:flex;align-items:center;gap:5px}
</style>
</head>
<body>

<!-- Cover -->
<section class="slide col-a row-1">
  <div class="wordmark abs" style="left:20px;top:18px"><span class="mark"></span>BRENVIK</div>
  <h1 class="cover-title">Enlightened<br>Engineering</h1>
  <div class="cover-date mono"><i></i>10 March 2026</div>
  <div class="photo" role="img" aria-label="Laser slicing machine head above a silicon wafer" style="left:232px;top:0;width:240px;height:265px;background:linear-gradient(160deg,#0c0d10 0%,var(--photo-mid) 45%,#23283a 70%,#151820 100%)"></div>
</section>

<!-- Section divider -->
<section class="slide col-b row-1 section">
  <h2 class="section-title">Brenvik Statistics</h2>
  <div class="footer on-blue"><span class="dot"></span>2026 BRENVIK SYSTEMS<span class="line"></span>05</div>
</section>

<!-- Agenda -->
<section class="slide col-a row-2">
  <h2 class="slide-title">Agenda</h2>
  <ol class="agenda-list">
    <li><span>1.</span>Introduction</li>
    <li><span>2.</span>About Us</li>
    <li><span>3.</span>Our Services</li>
    <li><span>4.</span>Statistics</li>
    <li><span>5.</span>Timeline</li>
    <li><span>6.</span>Thank You</li>
  </ol>
  <div class="photo" role="img" aria-label="Clean manufacturing hall with glass-enclosed production cells" style="left:225px;top:20px;width:226px;height:217px;background:linear-gradient(180deg,#d9dde2 0%,#9ea4ab 45%,#5a5f66 75%,#b7b9bc 100%)"></div>
  <div class="footer"><span class="dot"></span>2026 BRENVIK SYSTEMS<span class="line"></span>02</div>
</section>

<!-- Statistics -->
<section class="slide col-b row-2">
  <h2 class="slide-title">Statistics</h2>
  <div class="text-block" style="left:19px;top:71px;width:205px;gap:6px">
    <p class="lead">Harnessing the power of light to deliver precision, scalability, and sustainability across every stage of production.</p>
    <p class="body">Nemo enim ipsam voluptatem quia voluptas sit aspernatur aut odit aut fugit, sed quia equuntur magni dolores eos qui ratione voluptatem sequi nesciunt. Neque porro quisquam est.</p>
  </div>
  <svg class="abs" style="left:0;top:0" width="472" height="265" viewBox="0 0 472 265" aria-label="Pie chart">
    <path d="M338 138 L338 225 A87 87 0 0 1 338 51 Z" fill="var(--slice-1)"/>
    <path d="M338 138 L338 51 A87 87 0 0 1 397.6 74.6 Z" fill="var(--slice-2)"/>
    <path d="M338 138 L397.6 74.6 A87 87 0 0 1 425 138 Z" fill="var(--slice-3)"/>
    <path d="M338 138 L425 138 A87 87 0 0 1 338 225 Z" fill="var(--slice-4)"/>
    <line x1="366" y1="46" x2="366" y2="55" stroke="var(--ink)" stroke-width=".5"/>
  </svg>
  <div class="pie-label" style="left:366px;top:22px"><b>12%</b>Magni dolores</div>
  <div class="pie-label" style="left:393px;top:103px"><b>13%</b>Magni dolores</div>
  <div class="pie-label" style="left:295px;top:121px;color:#fff"><b>50%</b>Magni dolores</div>
  <div class="pie-label" style="left:372px;top:159px"><b>25%</b>Magni dolores</div>
  <div class="footer"><span class="dot"></span>2026 BRENVIK SYSTEMS<span class="line"></span>06</div>
</section>

<!-- Introduction -->
<section class="slide col-a row-3">
  <h2 class="slide-title">Introduction</h2>
  <div class="text-block" style="left:19px;top:70px;width:284px;gap:9px">
    <p class="lead">For industries driving tech forward, Brenvik is the most advanced laser- based manufacturing partner, unlocking the power of light for cleaner, smarter, more scalable production.</p>
    <p class="body">Using proprietary laser wafering technology, we deliver ultra-clean, ultra-efficient wafers that outperform traditional methods in speed, precision, and material yield.</p>
  </div>
  <div class="photo" role="img" aria-label="Line drawing of the laser wafering machine" style="left:309px;top:0;width:163px;height:265px;background:linear-gradient(180deg,#f6f6f7,#eeeef0)"></div>
  <div class="footer"><span class="dot"></span>2026 BRENVIK SYSTEMS<span class="line"></span>03</div>
</section>

<!-- Timeline -->
<section class="slide col-b row-3">
  <h2 class="slide-title">Timeline</h2>
  <p class="tl-note" style="left:94px;top:78px;width:80px">Initial SiC laser slicing tool demonstrated and Santa Clara CA production site build out.</p>
  <p class="tl-note" style="left:251px;top:78px;width:80px">Key customer qualification and IATF automotive quality certification.</p>
  <p class="tl-note" style="left:408px;top:78px;width:50px">High-volume production scale-up In Malaysia.</p>

  <div class="tl-year" style="left:20px"><i></i>2014</div>
  <div class="tl-link" style="left:63px;width:25px"></div>
  <div class="tl-year" style="left:94px"><i></i>2022</div>
  <div class="tl-link" style="left:141px;width:25px"></div>
  <div class="tl-year" style="left:174px"><i></i>2024</div>
  <div class="tl-link" style="left:220px;width:25px"></div>
  <div class="tl-year" style="left:251px"><i></i>2025</div>
  <div class="tl-link" style="left:299px;width:25px"></div>
  <div class="tl-year" style="left:331px"><i></i>2026</div>
  <div class="tl-link" style="left:378px;width:25px"></div>
  <div class="tl-year" style="left:408px"><i></i>2027</div>

  <p class="tl-note" style="left:20px;top:158px;width:80px">Spin out from Westbrook University. Silicon Valley Headquarters.</p>
  <p class="tl-note" style="left:174px;top:158px;width:80px">Top tier US VC Series B $80M USD funding. 200mm production capability.</p>
  <p class="tl-note" style="left:331px;top:158px;width:80px">Initial production manufacturing with Tier 1 automotive customer out of California production line.</p>
  <div class="footer"><span class="dot"></span>2026 BRENVIK SYSTEMS<span class="line"></span>07</div>
</section>

<!-- About Us -->
<section class="slide col-a row-4">
  <h2 class="slide-title">About Us</h2>
  <div class="text-block" style="left:19px;top:71px;width:205px;gap:6px">
    <p style="font-size:12.7px;line-height:17.5px;margin-left:1px">Built at Westbrook,<br>backed by visionaries</p>
    <p class="body">Founded in 2014 as a Westbrook spinout, we combine breakthrough research with real-world execution. With $132M in funding from leading VCs and government partners, we're building the backbone of an electrified future.</p>
  </div>

  <div class="feature" style="top:72px">
    <div class="icon"><svg width="18" height="18" viewBox="0 0 24 24" fill="none" stroke="#fff" stroke-width="1.2"><path d="M9 16c0-2-3-3.5-3-7a6 6 0 0 1 12 0c0 3.5-3 5-3 7z"/><path d="M9.5 18.5h5M10 21h4"/><path d="M12 1v1.5M3 9h1.5M19.5 9H21M5 3.5l1 1M19 3.5l-1 1"/></svg></div>
    <div><h3>Westbrook innovation</h3><p>Academic rigor meets manufacturing execution</p></div>
  </div>
  <div class="feature" style="top:125px">
    <div class="icon"><svg width="18" height="18" viewBox="0 0 24 24" fill="none" stroke="#fff" stroke-width="1.2"><path d="M12 3l2.7 5.6 6.1.8-4.4 4.3 1 6.1L12 17l-5.4 2.8 1-6.1-4.4-4.3 6.1-.8z"/></svg></div>
    <div><h3>Industry leadership</h3><p>Backed by VCs and energy agencies driving deep-tech innovation</p></div>
  </div>
  <div class="feature" style="top:179px">
    <div class="icon"><svg width="18" height="18" viewBox="0 0 24 24" fill="none" stroke="#fff" stroke-width="1.2"><circle cx="12" cy="8" r="3.5"/><path d="M5 20c0-4 3-6.5 7-6.5s7 2.5 7 6.5z"/><path d="M6.5 11a2.5 2.5 0 0 1 0-5M17.5 11a2.5 2.5 0 0 0 0-5M2 18c0-2.5 1.5-4 3.5-4.5M22 18c0-2.5-1.5-4-3.5-4.5"/></svg></div>
    <div><h3>Expert team</h3><p>Decades of experience in laser physics and advanced materials</p></div>
  </div>
  <div class="footer"><span class="dot"></span>2026 BRENVIK SYSTEMS<span class="line"></span>04</div>
</section>

<!-- Closing -->
<section class="slide col-b row-4">
  <div class="wordmark abs" style="left:20px;top:22px"><span class="mark"></span>BRENVIK</div>
  <h2 class="abs" style="left:18px;top:175px;font-size:30px;font-weight:500;letter-spacing:-.3px">Thank You</h2>
  <div class="contact mono" style="top:221px"><i></i>info@brenvik-systems.example</div>
  <div class="contact mono" style="top:234px"><i></i>1480 Verano Ave,Santa Clara, CA 95054</div>
  <div class="photo" role="img" aria-label="Laser nozzle focusing a beam onto a wafer" style="left:232px;top:0;width:240px;height:265px;background:linear-gradient(170deg,#c9d0da 0%,#8794a8 35%,#3c4a63 65%,#1a2233 100%)"></div>
</section>

</body>
</html>
```